Property management company looking for modern card design

We at Blue Heron Partners provides property management services for its residential and commercial properties, with expertise in all categories of multifamily, industrial and office projects throughout California.

We need a business card design that is professional and modern designed business card. In our field, clients get hundreds of business cards, we would like our card to stand out.

Please avoid small print.

Target Market(s)

Professionals and high end clients

Industry/Entity Type

Financial Planning

Contact Information for Business Card

Company Name: Blue Heron Partners, Name, email, license #, phone number, website blueheronpartners.com

Font styles to use
Sans Serif

Requirements
Must have
• The card design needs to be adaptable because there is a possibly we will be expanding into different sectors other than real estate. The card design should be focused on financial planning and asset management.
Nice to have
• Modern and simple business card. Eye catching. Non-standard size/shaped cards would be great.
• blueheronpartners.com
Should not have
• Too many bright color or any pictures or shapes of real estate stuff.

```html
<!DOCTYPE html>
<html lang="en">
<head>
<meta charset="utf-8">
<title>Blue Heron Partners – Business Cards</title>
<link rel="stylesheet" href="https://fonts.googleapis.com/css2?family=Ubuntu:wght@400;500;700&family=Arimo:wght@700&display=swap">
<style>
  :root {
    --backdrop: #8a5a2c;
    --paper: #eff1ef;
    --brand-red: #a80000;
    --accent-red: #e3152d;
    --ink: #1f2426;
    --ink-soft: #4f5254;
  }
  html, body {
    margin: 0;
    padding: 0;
    overflow: hidden;
  }
  .canvas {
    position: relative;
    width: 900px;
    height: 1200px;
    background: var(--backdrop);
    overflow: hidden;
    font-family: "Ubuntu", sans-serif;
  }
  .card {
    position: absolute;
    background: var(--paper);
    box-shadow: 0 6px 18px rgba(0,0,0,0.25);
    overflow: hidden;
  }
  .card--front {
    left: 315px;
    top: 142px;
    width: 301px;
    height: 527px;
  }
  .card--back {
    left: 186px;
    top: 741px;
    width: 527px;
    height: 301px;
  }
  .brand-dot {
    position: absolute;
    width: 52px;
    height: 52px;
    border-radius: 50%;
    background: var(--accent-red);
  }
  .brand-name {
    position: absolute;
    left: 0;
    right: 0;
    text-align: center;
    font-family: "Ubuntu", sans-serif;
    font-weight: 500;
    color: var(--brand-red);
    white-space: nowrap;
  }
  .card--front .brand-dot { left: 124px; top: 72px; }
  .card--front .brand-name { top: 170px; font-size: 19px; letter-spacing: 2px; }
  .card--back .brand-dot { left: 237px; top: 86px; }
  .card--back .brand-name { top: 184px; font-size: 25px; letter-spacing: 4px; }

  .bar {
    position: absolute;
    background: var(--brand-red);
  }
  .bar--top { left: 158px; top: 238px; width: 115px; height: 16px; }
  .bar--block { left: 158px; top: 322px; width: 115px; height: 91px; }
  .bar--rule { left: 158px; top: 478px; width: 115px; height: 6px; }
  .bar--foot { left: 158px; top: 509px; width: 115px; height: 18px; }
  .bar--back-foot { left: 0; bottom: 0; width: 100%; height: 16px; }

  .person, .contact {
    position: absolute;
    right: 32px;
    text-align: right;
    margin: 0;
    white-space: nowrap;
  }
  .person__name {
    top: 260px;
    font-size: 31px;
    font-weight: 500;
    color: var(--ink);
  }
  .person__role {
    top: 297px;
    font-size: 13px;
    color: var(--ink);
  }
  .contact {
    font-size: 12.5px;
    font-weight: 500;
    color: var(--ink);
  }
  .contact--email { top: 419px; font-size: 12px; }
  .contact--phone { top: 442px; }
  .contact--license { top: 464px; }
  .website {
    position: absolute;
    font-family: "Arimo", sans-serif;
    font-weight: 700;
    white-space: nowrap;
    margin: 0;
  }
  .card--front .website {
    right: 32px;
    top: 484px;
    font-size: 16px;
    color: var(--ink);
  }
  .card--back .website {
    left: 0;
    right: 0;
    text-align: center;
    top: 254px;
    font-size: 18px;
    color: var(--ink-soft);
  }
</style>
</head>
<body>
<main class="canvas">

  <section class="card card--front" aria-label="Business card front">
    <div class="brand-dot" aria-hidden="true"></div>
    <p class="brand-name" style="margin:0">Blue Heron Partners</p>

    <div class="bar bar--top"></div>
    <h1 class="person person__name">Daniel Reyes</h1>
    <p class="person person__role">managing director</p>
    <div class="bar bar--block"></div>

    <p class="contact contact--email">daniel.reyes@blueheronpartners.com</p>
    <p class="contact contact--phone">555-555-5555</p>
    <p class="contact contact--license">License Nr:000001</p>
    <div class="bar bar--rule"></div>
    <p class="website">blueheronpartners.com</p>
    <div class="bar bar--foot"></div>
  </section>

  <section class="card card--back" aria-label="Business card back">
    <div class="brand-dot" aria-hidden="true"></div>
    <p class="brand-name" style="margin:0">Blue Heron Partners</p>
    <p class="website">blueheronpartners.com</p>
    <div class="bar bar--back-foot"></div>
  </section>

</main>
</body>
</html>
```